July 2022 Industrial Manufacturer Product Expo Mexico City

We manufacture large screws and fastners for large Mining equipment, Trains, large ships, airplanes, wind turbines, and so on. We also do custom work base on the customer needs. No matter the size we can make it.
We have a Expo coming up with companies all over the world. We have to stand out we are a family own business so our customer service will be above and beyond anyone can provide. We do not have a sales force to push our products and services we provide one on one service.
Plus@!! I'm looking for anything that you designers can come up with if it was your company to put on a business card, plus i want to do a 1 or 2 sided pamphlet, and then a website. We make Speciality Bolts for large mining equipment these bolts can be 3 to 4 foot long!!! Plus fasteners, Nuts, washers, any, size, strengths, special materials, we offer more of a ono on one customer service, We are a small company, family own, but can fulfill any type of orders. We can also provide special time lines for emergency orders. "We keep the machines running we here at KRV don't believe in down time" We want to hear any slogan based on our company to stand out.
Thanks i really appreciate all your work and options that we have to pick on. Plus just a thought we could possibly want to entertain a experience Marketing internet help maybe a employment possibility. Thanks

I need 2 cards one in Spanish and English Like the steel back ground maybe send me in some bright red and blue writing Same with the Black cards Please remove the word Military The logo KRV maybe integrate a picture of a Bolt 🔩 Thank you

Still looking for I need 2 cards one in Spanish and English Like the steel back ground maybe send me in some bright red and blue writing Same with the Black cards try bright writing Please remove the word Military The logo KRV maybe integrate a picture of a Bolt 🔩 Plus will need the company to make a brochure and website next Thank you

Target Market(s)

Large Mining, Ship, Train, Green Energy, VELM, and Government equipment. Throughout the World

Industry/Entity Type

We can Custom Manufacture any type of Fastners for Mining equipment, Trains, Ships, Green energy, Governments, or military projects. wind turbines,

Contact Information for Business Card

I attached the name and contact info that's on a card, plus the Company Logo. Would like industrial looking background with Bright Colors that will stand out!! If we can insert somewhere maybe on back that we "Custom Manufacture Any Size or Quantity Fastners for Large Mining Equipment, Trains, Ships, Green Energy Equipment or Government Projects

Font styles to use
Other font styles liked:
• You Pick, has to be bold, colorful standout, Professional looking Beable to read it.

Colors

Designer to choose colors to be used in the design.

Requirements
Must have
• Need in Spanish and English TO STANDOUT FROM THE REST OF THE EXPO!! See Business card details, Rounded corners
Nice to have
• Can i see some of the darker cards with Bright Red and Blue letters I like to see the different type of card material, heavy thickness, plastic, transparent, Metal types, Bright Colors, I saw like Raised letters like on the logo.

```html
<!DOCTYPE html>
<html lang="en">
<head>
<meta charset="utf-8">
<title>KRV Business Cards – English &amp; Spanish</title>
<link rel="stylesheet" href="https://fonts.googleapis.com/css2?family=PT+Sans:wght@400;700&display=swap">
<style>
  :root {
    --backdrop: #2b2b2b;
    --card: #b9b9b9;
    --label-red: #b01116;
    --bright-red: #e41414;
    --navy: #1b2a7c;
    --brand-blue: #0d4fb0;
    --rule: #7d7d7d;
    --bolt-light: #cfcfcf;
    --bolt-dark: #8e8e8e;
  }
  * { box-sizing: border-box; margin: 0; padding: 0; }
  html, body {
    width: 1200px; height: 833px; overflow: hidden;
    background: var(--backdrop);
    font-family: "PT Sans", sans-serif;
  }
  .sheet { position: relative; width: 1200px; height: 833px; }
  .language-label {
    position: absolute; top: 76px; width: 401px; text-align: center;
    font-size: 37px; font-weight: 700; color: var(--label-red);
  }
  .label-english { left: 138px; }
  .label-spanish { left: 654px; }
  .card {
    position: absolute; width: 401px; height: 248px;
    background: var(--card); border-radius: 8px; overflow: hidden;
  }
  .card-en-front { left: 138px; top: 157px; }
  .card-es-front { left: 654px; top: 157px; }
  .card-en-back  { left: 138px; top: 430px; }
  .card-es-back  { left: 652px; top: 430px; }
  .brand {
    position: absolute; left: 0; right: 0; text-align: center;
    font-weight: 700; font-size: 52px; letter-spacing: 6px;
    color: var(--brand-blue); line-height: 1;
  }
  .card-front .brand { top: 42px; }
  .card-back .brand { top: 56px; z-index: 2; }
  .brand-mark {
    display: inline-block; width: 14px; height: 14px; margin-right: 10px;
    background: var(--brand-blue); vertical-align: middle;
  }
  .holder-name {
    position: absolute; left: 0; right: 0; text-align: center;
    color: var(--navy); font-weight: 400;
  }
  .card-en-front .holder-name { top: 136px; font-size: 17px; font-weight: 700; }
  .card-es-front .holder-name { top: 157px; font-size: 15px; }
  .holder-title {
    position: absolute; left: 0; right: 0; top: 158px; text-align: center;
    font-size: 13px; color: var(--bright-red);
  }
  .divider {
    position: absolute; left: 175px; width: 51px; height: 1px; background: var(--rule);
  }
  .card-en-front .divider { top: 185px; }
  .card-es-front .divider { top: 187px; }
  .phone {
    position: absolute; left: 0; right: 0; top: 196px; text-align: center;
    font-size: 13px; color: var(--bright-red); letter-spacing: 0.3px;
  }
  .phone svg { width: 11px; height: 11px; vertical-align: -1px; margin-right: 4px; }
  .bolt-visual {
    position: absolute; left: 36px; top: 2px; width: 360px; height: 240px;
    background: linear-gradient(160deg, var(--bolt-light) 0%, #a9a9a9 45%, var(--bolt-dark) 100%);
    opacity: 0.55; border-radius: 40px 20px 30px 90px;
  }
  .services {
    position: absolute; left: 0; right: 0; text-align: center;
    font-size: 13px; line-height: 16.4px; color: var(--bright-red); z-index: 2;
  }
  .card-en-back .services { top: 155px; }
  .card-es-back .services { top: 133px; }
</style>
</head>
<body>
<main class="sheet">
  <h2 class="language-label label-english">English</h2>
  <h2 class="language-label label-spanish">Spanish</h2>

  <section class="card card-front card-en-front">
    <div class="brand"><span class="brand-mark"></span>KRV</div>
    <p class="holder-name">Dana Whitfield</p>
    <p class="holder-title">Director of Sales &amp; Marketing</p>
    <div class="divider"></div>
    <p class="phone"><svg viewBox="0 0 24 24" aria-hidden="true"><path fill="#1b2a7c" d="M6.6 10.8c1.4 2.8 3.8 5.1 6.6 6.6l2.2-2.2c.3-.3.7-.4 1-.2 1.1.4 2.3.6 3.6.6.6 0 1 .4 1 1V20c0 .6-.4 1-1 1C10.6 21 3 13.4 3 4c0-.6.4-1 1-1h3.5c.6 0 1 .4 1 1 0 1.3.2 2.5.6 3.6.1.3 0 .7-.2 1L6.6 10.8z"/></svg>011521(555)0148392</p>
  </section>

  <section class="card card-front card-es-front">
    <div class="brand"><span class="brand-mark"></span>KRV</div>
    <p class="holder-name">Gerente Gral. Lucía Ferrer Ortega</p>
    <div class="divider"></div>
    <p class="phone"><svg viewBox="0 0 24 24" aria-hidden="true"><path fill="#1b2a7c" d="M6.6 10.8c1.4 2.8 3.8 5.1 6.6 6.6l2.2-2.2c.3-.3.7-.4 1-.2 1.1.4 2.3.6 3.6.6.6 0 1 .4 1 1V20c0 .6-.4 1-1 1C10.6 21 3 13.4 3 4c0-.6.4-1 1-1h3.5c.6 0 1 .4 1 1 0 1.3.2 2.5.6 3.6.1.3 0 .7-.2 1L6.6 10.8z"/></svg>011521(555)0148392</p>
  </section>

  <section class="card card-back card-en-back">
    <div class="bolt-visual" role="img" aria-label="Faded photo of a large steel hex bolt lying diagonally"></div>
    <div class="brand"><span class="brand-mark"></span>KRV</div>
    <p class="services">Custom Manufacture Any Size or<br>Quantity Fastners for Large&nbsp; Mining<br>Equipment Trains, Ships, Green Energy<br>Equipment or Government Projects</p>
  </section>

  <section class="card card-back card-es-back">
    <div class="bolt-visual" role="img" aria-label="Foto tenue de un perno de acero hexagonal grande en diagonal"></div>
    <div class="brand"><span class="brand-mark"></span>KRV</div>
    <p class="services">Fabricación especializada y Maquinados<br>Proyectos<br>Mineros<br>Ferroviarios<br>Construcción<br>Automotrices</p>
  </section>
</main>
</body>
</html>
```